Martial Arts Website

Redevelopment of existing martial arts website.

The academy teaches traditional shaolin martial arts, including Shaolin Kung Fu, Wu Shu, Tai Chi, Qigong and Wing Chun and the site needs to reflect the traditional roots (eg, no tacky boxing imagery)

Existing website is www.copperlantern.com.au to get a feel for the desired color scheme (black, green and red). The exact colors can be tweaked though. Please only reuse the logo and font (Karate) - there isnt anything else from the current design that needs to remain.

The current website includes links to a ClipHarbor channel that includes demonstrations of the training conducted to better guide the design.

The new website site map will be:
1. Home
2. Programs - summary page describing each form of training
a. Tiny Otters
b. Kids Kung Fu
c. Youth Kung Fu
d. Adults Kung Fu
e. Wing Chun
f. Tai Chi & Qigong
g. Weaponry Classes
h. 72 Arts of Shaolin Conditioning Program
i. Acrobatics and Wu Shu
j. Fitness Boxing
3. Timetable
4. Coaches - summary page describing all coaches
a. Sifu (Master)
b. Sihing Kit
c. Sihing Sam
d. Sihing Marcus
X. ... up to 10 or so coaches
5. Member Zone
6. Contact Us
Updates

Logo now attached to brief - sorry I only have it in PDF

Just to clarify, I am only expecting a PSD design - no HTML required

Reason: Thanks for the designs, we love a lot of them just require a little extra time to tweak the designs and establish the potential. Thanks for your understanding and efforts.

Target Market(s)

Parents, teenagers, young adults, adults, elderly

Industry/Entity Type

Training

Requirements
Must have
• Chinese kung fu dragon imagery throughout the background
Links to Chatterly and ClipHarbor channel
Promo/icon in the header "Try 2 free classes now"
Home page should include an embedded ClipHarbor video

```html
<!DOCTYPE html>
<html lang="en">
<head>
<meta charset="utf-8">
<title>Copper Lantern Martial Arts Academy – Member Zone</title>
<link rel="stylesheet" href="https://fonts.googleapis.com/css2?family=Arimo:ital,wght@0,400;0,700;1,400;1,700&family=Cinzel+Decorative:wght@700;900&family=Crimson+Text:wght@600&display=swap">
<style>
:root{
  --black:#000;
  --green:#2f8a2f;
  --green-dark:#1f5e1f;
  --green-logo:#2e9a2e;
  --red:#a80000;
  --red-nav:#b30f0f;
  --white:#fff;
  --grey-side-top:#8a8a8a;
  --grey-side-bot:#5a5a5a;
  --text-dark:#222;
  --footer-line:#999;
}
*{margin:0;padding:0;box-sizing:border-box}
html,body{width:1200px;height:1160px;overflow:hidden;background:var(--black);font-family:Arimo,Arial,sans-serif}
.page{position:relative;width:1200px;height:1160px}
.abs{position:absolute}

/* header */
.brand{left:0;top:0;width:1200px;height:178px;text-align:center}
.brand-name{position:absolute;left:0;width:1200px;top:58px;font-family:"Cinzel Decorative",serif;font-weight:900;font-size:50px;color:var(--green-logo);letter-spacing:2px}
.brand-sub{position:absolute;left:0;width:1200px;top:121px;font-family:"Crimson Text",serif;font-weight:600;font-size:19px;letter-spacing:4px;color:var(--red)}
.brand-tag{position:absolute;left:0;width:1200px;top:145px;font-size:11px;letter-spacing:2.4px;color:var(--white)}

.nav{left:0;top:178px;width:1200px;height:40px;background:var(--white)}
.nav a{position:absolute;top:11px;font-size:13px;color:#444;text-decoration:none}
.nav .sep{position:absolute;top:6px;width:1px;height:26px;background:#bbb}
.nav .active{position:absolute;left:698px;top:-15px;width:103px;height:44px;background:var(--red-nav);color:var(--white);padding-top:25px;text-align:center;font-size:13px}

.band{left:0;top:218px;width:1200px;height:61px;background:linear-gradient(#2a9a2a,#1c6d1c)}
.band h1{position:absolute;left:0;width:1200px;top:14px;text-align:center;font-family:"Cinzel Decorative",serif;font-weight:900;font-size:26px;color:var(--white)}

.crumbs{left:234px;top:286px;font-size:13px;color:var(--white)}

.art{left:225px;top:310px;width:755px;height:525px;border-radius:40px;background:radial-gradient(ellipse at 50% 50%,#3f5a1c 0%,#2a3a12 45%,#120f05 75%,#000 100%)}
.scroll-l,.scroll-r{top:815px;width:220px;height:45px;background:linear-gradient(90deg,#333,#111)}
.scroll-l{left:0}
.scroll-r{left:978px;background:linear-gradient(90deg,#111,#444)}

/* login */
.login{left:415px;top:405px;width:370px;height:370px;background:var(--white);border:8px solid #8a6a2c;border-radius:6px;outline:2px solid #c9a24e}
.login h2{position:absolute;left:18px;top:26px;font-style:italic;font-weight:700;font-size:16px;color:var(--text-dark)}
.login label{position:absolute;left:17px;font-size:14px;color:var(--text-dark)}
.field{position:absolute;left:18px;width:314px;height:21px;border:1px solid #777;background:#f5f5f5}
.remember{position:absolute;left:18px;top:182px;font-size:14px;letter-spacing:.4px;color:var(--text-dark)}
.remember i{display:inline-block;width:11px;height:11px;border:1px solid #777;border-radius:2px;margin-right:6px;vertical-align:-1px}
.small-link{position:absolute;font-size:9.5px;color:var(--text-dark);text-decoration:underline;letter-spacing:.3px}
.btn{position:absolute;top:260px;height:22px;background:linear-gradient(#3e8a2e,#22591a);color:var(--white);font-size:12.5px;text-align:center;padding-top:4px}

/* sidebar */
.side{left:966px;top:218px;width:220px;height:417px;background:linear-gradient(var(--grey-side-top),var(--grey-side-bot))}
.side h3{position:absolute;left:0;width:220px;top:11px;text-align:center;font-family:"Crimson Text",serif;font-weight:600;font-size:19px;color:var(--white)}
.side .rule{position:absolute;left:20px;top:39px;width:174px;border-top:1px dotted #ccc}
.class{position:absolute;left:18px;color:var(--white);font-style:italic}
.class svg{position:absolute;left:0;top:0}
.class b{position:absolute;left:36px;top:-2px;white-space:nowrap;font-size:13px}
.class span{position:absolute;left:36px;top:13px;white-space:nowrap;font-size:10px}
.try{left:966px;top:635px;width:220px;height:32px;background:linear-gradient(#3a9a3a,#237323);color:var(--white);font-weight:700;font-size:14px;padding:8px 0 0 11px}

/* footer */
.redband{left:0;top:860px;width:1200px;height:28px;background:var(--red)}
.footer{left:0;top:888px;width:1200px;height:185px;background:var(--white)}
.footer h4{position:absolute;top:19px;font-family:"Crimson Text",serif;font-weight:600;font-size:17px;color:#111}
.footer .div{position:absolute;top:18px;height:150px;border-left:1px dashed #777}
.item{position:absolute;font-size:12px;color:var(--text-dark);line-height:14px}
.item strong{font-weight:700}
.badge{position:absolute}
.like{position:absolute;left:653px;top:145px;width:50px;height:23px;border:1px solid #ccd;border-radius:3px;background:#f2f4f8;font-size:12px;color:#3b5a9a;text-align:center;padding-top:4px}

.bottom-line{left:5px;top:1113px;width:1170px;border-top:1px dotted #555}
.copyright{left:4px;top:1126px;font-size:12.5px;color:#999}
</style>
</head>
<body>
<div class="page">

  <header class="abs brand">
    <div class="brand-name">COPPER LANTERN</div>
    <div class="brand-sub">MARTIAL ARTS ACADEMY</div>
    <div class="brand-tag">TRADITIONAL KUNG FU &amp; TAI CHI TRAINING CENTRE</div>
  </header>

  <nav class="abs nav">
    <a style="left:310px">HOME</a><i class="sep" style="left:376px"></i>
    <a style="left:394px">PROGRAMS</a><i class="sep" style="left:482px"></i>
    <a style="left:500px">TIMETABLE</a><i class="sep" style="left:585px"></i>
    <a style="left:605px">COACHES</a><i class="sep" style="left:686px"></i>
    <span class="active">MEMBER ZONE</span><i class="sep" style="left:815px"></i>
    <a style="left:831px">CONTACT US</a>
  </nav>

  <div class="abs band"><h1>Member Zone</h1></div>

  <div class="abs crumbs">Home &nbsp;&gt;&nbsp; Member Zone</div>

  <div class="abs art" role="img" aria-label="Two green Chinese dragons coiled around flaming pillars, holding pearls, framing the login panel"></div>
  <div class="abs scroll-l" role="img" aria-label="Faded Chinese calligraphy strip"></div>
  <div class="abs scroll-r" role="img" aria-label="Faded Chinese calligraphy strip"></div>

  <form class="abs login">
    <h2>Member Login</h2>
    <label style="top:66px">Login ID:</label>
    <div class="field" style="top:87px"></div>
    <label style="top:121px">Password:</label>
    <div class="field" style="top:144px"></div>
    <div class="remember"><i></i>Remember Password</div>
    <span class="small-link" style="left:84px;top:223px">Remove Saved Login ID and Password</span>
    <span class="btn" style="left:85px;width:61px">LOGIN</span>
    <span class="btn" style="left:186px;width:85px">REGISTER</span>
    <span class="small-link" style="left:15px;top:325px">Lost Password</span>
    <span class="small-link" style="left:307px;top:325px">Help</span>
  </form>

  <aside class="abs side">
    <h3>ALL CLASSES</h3><div class="rule"></div>
    <div class="class" style="top:48px"><svg width="20" height="20"><circle cx="10" cy="10" r="8" fill="#c21a1a" stroke="#7a0d0d"/><path d="M5 10h7M9 6.5l3.5 3.5L9 13.5" stroke="#fff" stroke-width="2" fill="none"/></svg><b>Tiny Otters</b><span>Ages 4 - 6</span></div>
    <div class="class" style="top:86px"><svg width="20" height="20"><circle cx="10" cy="10" r="8" fill="#c21a1a" stroke="#7a0d0d"/><path d="M5 10h7M9 6.5l3.5 3.5L9 13.5" stroke="#fff" stroke-width="2" fill="none"/></svg><b>Kids Kung Fu</b><span>Ages 6 - 11</span></div>
    <div class="class" style="top:124px"><svg width="20" height="20"><circle cx="10" cy="10" r="8" fill="#c21a1a" stroke="#7a0d0d"/><path d="M5 10h7M9 6.5l3.5 3.5L9 13.5" stroke="#fff" stroke-width="2" fill="none"/></svg><b>Youth Kung Fu</b><span>Ages 11 - 15</span></div>
    <div class="class" style="top:161px"><svg width="20" height="20"><circle cx="10" cy="10" r="8" fill="#c21a1a" stroke="#7a0d0d"/><path d="M5 10h7M9 6.5l3.5 3.5L9 13.5" stroke="#fff" stroke-width="2" fill="none"/></svg><b>Adults Kung Fu</b><span>Ages 15 &amp; over</span></div>
    <div class="class" style="top:199px"><svg width="20" height="20"><circle cx="10" cy="10" r="8" fill="#c21a1a" stroke="#7a0d0d"/><path d="M5 10h7M9 6.5l3.5 3.5L9 13.5" stroke="#fff" stroke-width="2" fill="none"/></svg><b>Wing Chun</b><span>Ages 13 &amp; over</span></div>
    <div class="class" style="top:237px"><svg width="20" height="20"><circle cx="10" cy="10" r="8" fill="#c21a1a" stroke="#7a0d0d"/><path d="M5 10h7M9 6.5l3.5 3.5L9 13.5" stroke="#fff" stroke-width="2" fill="none"/></svg><b>Tai Chi &amp; Qigong</b><span>All ages</span></div>
    <div class="class" style="top:274px"><svg width="20" height="20"><circle cx="10" cy="10" r="8" fill="#c21a1a" stroke="#7a0d0d"/><path d="M5 10h7M9 6.5l3.5 3.5L9 13.5" stroke="#fff" stroke-width="2" fill="none"/></svg><b>Weaponry Classes</b><span>Ages 5 and over</span></div>
    <div class="class" style="top:313px"><svg width="20" height="20"><circle cx="10" cy="10" r="8" fill="#c21a1a" stroke="#7a0d0d"/><path d="M5 10h7M9 6.5l3.5 3.5L9 13.5" stroke="#fff" stroke-width="2" fill="none"/></svg><b>72 Arts of Shaolin</b><span>Conditioning Program</span></div>
    <div class="class" style="top:351px"><svg width="20" height="20"><circle cx="10" cy="10" r="8" fill="#c21a1a" stroke="#7a0d0d"/><path d="M5 10h7M9 6.5l3.5 3.5L9 13.5" stroke="#fff" stroke-width="2" fill="none"/></svg><b>Acrobatics and Wu Shu</b><span>Performance Team</span></div>
    <div class="class" style="top:387px"><svg width="20" height="20"><circle cx="10" cy="10" r="8" fill="#c21a1a" stroke="#7a0d0d"/><path d="M5 10h7M9 6.5l3.5 3.5L9 13.5" stroke="#fff" stroke-width="2" fill="none"/></svg><b>Fitness Boxing</b></div>
  </aside>
  <div class="abs try">TRY 2 FREE CLASSES NOW! <svg width="10" height="14" style="vertical-align:-2px;margin-left:4px"><path d="M0 0L10 7L0 14Z" fill="#fff"/></svg></div>

  <div class="abs redband"></div>

  <footer class="abs footer">
    <h4 style="left:70px">Contact</h4>
    <svg class="badge" style="left:38px;top:64px" width="18" height="30"><rect x="2" y="1" width="14" height="27" rx="3" fill="none" stroke="#555" stroke-width="2"/><rect x="5" y="5" width="8" height="15" fill="#777"/><circle cx="9" cy="24" r="1.6" fill="#555"/></svg>
    <div class="item" style="left:70px;top:65px"><strong>Phone:</strong><br>(02) 47001234</div>
    <svg class="badge" style="left:30px;top:109px" width="28" height="19"><rect x="1" y="1" width="26" height="17" fill="none" stroke="#666" stroke-width="1.5"/><path d="M1 1L14 11L27 1M1 18L11 9M27 18L17 9" stroke="#666" stroke-width="1.5" fill="none"/></svg>
    <div class="item" style="left:70px;top:107px"><strong>Email:</strong><br>kwoon@copperlantern.com.au</div>
    <i class="div" style="left:277px"></i>

    <h4 style="left:367px">News &amp; Downloads</h4>
    <svg class="badge" style="left:334px;top:66px" width="20" height="24"><rect x="1" y="1" width="14" height="18" fill="#888"/><rect x="5" y="5" width="14" height="18" fill="#666"/></svg>
    <div class="item" style="left:368px;top:65px"><strong>Newsletter</strong><br>Click here to download</div>
    <svg class="badge" style="left:334px;top:104px" width="22" height="22"><circle cx="11" cy="11" r="9" fill="none" stroke="#777" stroke-width="2"/><circle cx="11" cy="11" r="3.5" fill="none" stroke="#777" stroke-width="2"/></svg>
    <div class="item" style="left:368px;top:107px"><strong>News &amp; Updates</strong><br>Click here to view</div>
    <i class="div" style="left:600px"></i>

    <h4 style="left:693px">Social Media</h4>
    <svg class="badge" style="left:648px;top:64px" width="34" height="34"><rect width="34" height="34" rx="4" fill="#b3261e"/></svg>
    <div class="item" style="left:694px;top:65px"><strong>ClipHarbor</strong><br>View our channel here</div>
    <svg class="badge" style="left:648px;top:104px" width="34" height="34"><rect width="34" height="34" rx="4" fill="#3b5a9a"/></svg>
    <div class="item" style="left:694px;top:107px"><strong>Chatterly</strong></div>
    <div class="item" style="left:694px;top:124px;font-size:11px;width:140px"><svg width="11" height="11" style="vertical-align:-1px"><rect width="11" height="11" rx="2" fill="#3b5a9a"/></svg> 222 people like this. Be<br>&nbsp;&nbsp;&nbsp;&nbsp;the first of your friends.</div>
    <span class="like">Like</span>
    <i class="div" style="left:899px"></i>

    <h4 style="left:942px">Alliances &amp; Accreditation</h4>
    <svg class="badge" style="left:983px;top:49px" width="67" height="48"><rect width="67" height="48" fill="#8a8a8a"/></svg>
    <svg class="badge" style="left:1068px;top:47px" width="52" height="52"><circle cx="26" cy="26" r="24" fill="#d61a1a" stroke="#111" stroke-width="3"/></svg>
    <svg class="badge" style="left:978px;top:108px" width="72" height="50"><ellipse cx="36" cy="22" rx="34" ry="20" fill="none" stroke="#111" stroke-width="3"/></svg>
    <svg class="badge" style="left:1070px;top:102px" width="48" height="50"><circle cx="24" cy="24" r="22" fill="#1f4fa8"/><circle cx="24" cy="24" r="11" fill="#d61a1a"/></svg>
  </footer>

  <div class="abs bottom-line"></div>
  <div class="abs copyright">Copyright © 2012 - Copper Lantern Martial Arts Pty Ltd. Kung Fu and Tai Chi Training Centre - Unit 7, 22 Harbour Lane, Westvale NSW 2790</div>
</div>
</body>
</html>
```